Unique Business Card Design

Unique Business Card design for our orthotic and prosthetic company. Our logo is on our website, color is light blue. Unique shape (artificial leg shaped, vertical, etc..) preferred. Logo, business name, individual name and basic demographics needed.

Industry/Entity Type

Business

Contact Information for Business Card

Logo, Industry, Phone # Logo, "Prosthetic & Orthotic Services" Place to add individual name and contact info

Colors
cee9f5

Requirements
Must have
• The icon must be there, placement of "Prosthetic & Orthotic Services" can be moved
Nice to have
• Like the mix of light blue, and a little darker blue. One design included the icons from my website which was a nice touch

```html
<!DOCTYPE html>
<html lang="en">
<head>
<meta charset="utf-8">
<title>Strideform Inc. – Business Card</title>
<link href="https://fonts.googleapis.com/css2?family=Source+Sans+3:wght@400;600&family=Cormorant+Garamond:ital,wght@1,600&display=swap" rel="stylesheet">
<style>
  :root {
    --page-bg: #e4e7ea;
    --card-top: #f1f4f7;
    --navy: #1b3c80;
    --band-dark: #1c4793;
    --band-light: #2d5fb4;
    --band-text: #dfe8f5;
    --zip-tone: #f0d9c8;
    --placeholder-top: #5a7fbf;
    --placeholder-bottom: #3a63a8;
  }
  * { margin: 0; padding: 0; box-sizing: border-box; }
  html, body { width: 1200px; height: 969px; overflow: hidden; }
  body {
    background: var(--page-bg);
    font-family: "Source Sans 3", sans-serif;
  }
  .card {
    position: absolute;
    left: 100px; top: 200px;
    width: 1000px; height: 566px;
    background: var(--card-top);
    box-shadow: 0 10px 30px rgba(0,0,0,0.15);
    overflow: hidden;
  }
  .company-name {
    position: absolute;
    left: 0; right: 0; top: 76px;
    text-align: center;
    font-size: 64px; font-weight: 600;
    letter-spacing: 1px;
    color: var(--navy);
    line-height: 1;
  }
  .company-rule {
    position: absolute;
    left: 226px; width: 548px; top: 168px; height: 4px;
    background: var(--navy);
  }
  .tagline {
    position: absolute;
    left: 0; right: 0; top: 180px;
    text-align: center;
    font-family: "Cormorant Garamond", serif;
    font-style: italic; font-weight: 600;
    font-size: 42px;
    color: var(--navy);
  }
  .contact-band {
    position: absolute;
    left: 0; right: 0; top: 318px; bottom: 0;
    background: linear-gradient(90deg, var(--band-dark), var(--band-light) 55%, var(--band-dark));
  }
  .holder {
    position: absolute; left: 46px; top: 52px;
    color: var(--band-text);
  }
  .holder-name { font-size: 31px; font-weight: 600; line-height: 1.1; }
  .holder-title { font-size: 22px; margin-top: 6px; }
  .address { position: absolute; left: 46px; top: 130px; color: var(--band-text); font-size: 25px; line-height: 40px; }
  .address .zip { color: var(--zip-tone); font-weight: 400; }
  .emblem-area {
    position: absolute; left: 400px; top: 330px;
    width: 200px; height: 222px;
    background: linear-gradient(180deg, var(--placeholder-top), var(--placeholder-bottom));
  }
  .contact-list {
    position: absolute; right: 32px; top: 20px;
    list-style: none;
    color: var(--band-text);
    font-size: 25px;
    text-align: right;
    line-height: 38px;
  }
  .contact-list li { display: flex; justify-content: flex-end; align-items: center; gap: 10px; }
  .contact-list svg { width: 24px; height: 24px; fill: var(--band-text); }
</style>
</head>
<body>
  <div class="card">
    <div class="company-name">STRIDEFORM INC.</div>
    <div class="company-rule"></div>
    <div class="tagline">Prosthetic &amp; Orthotic Services</div>

    <div class="contact-band">
      <div class="holder">
        <div class="holder-name">Mirela Tovanek</div>
        <div class="holder-title">CO LPO</div>
      </div>
      <div class="address">
        908 Harlan Ave.<br>
        Brooklyn, NY <span class="zip">11230</span>
      </div>
      <ul class="contact-list">
        <li>555.204.1800
          <svg viewBox="0 0 24 24"><path d="M6.6 10.8a15 15 0 0 0 6.6 6.6l2.2-2.2a1 1 0 0 1 1-.25 11.4 11.4 0 0 0 3.6.57 1 1 0 0 1 1 1V20a1 1 0 0 1-1 1A17 17 0 0 1 3 4a1 1 0 0 1 1-1h3.5a1 1 0 0 1 1 1c0 1.25.2 2.45.57 3.57a1 1 0 0 1-.25 1z"/></svg>
        </li>
        <li>555.204.3926
          <svg viewBox="0 0 24 24"><path d="M7 2h10a1.5 1.5 0 0 1 1.5 1.5v17A1.5 1.5 0 0 1 17 22H7a1.5 1.5 0 0 1-1.5-1.5v-17A1.5 1.5 0 0 1 7 2zm0 2v14h10V4zm5 15a1 1 0 1 0 0 2 1 1 0 0 0 0-2z"/></svg>
        </li>
        <li>555-3187402
          <svg viewBox="0 0 24 24"><path d="M7 2h8l3 3v5H7zM4 11h16a2 2 0 0 1 2 2v7H2v-7a2 2 0 0 1 2-2zm2 3v2h4v-2zm0 3v1h12v-1z"/></svg>
        </li>
        <li>www.strideforminc.com</li>
        <li>Mtovanek@strideforminc.com</li>
      </ul>
    </div>

    <div class="emblem-area" role="img" aria-label="Company emblem area"></div>
  </div>
</body>
</html>
```